Major infrastructure project needs a diagram designed

We need two simple diagrams created on Sydney's current (1) and future (2) intermodal terminal capacity and the number of shipping containers coming out of Port Kelvanna.

Please see attached file for full instructions (Word and PDF attached)

Shipping

```html
<!DOCTYPE html>
<html lang="en">
<head>
<meta charset="utf-8">
<title>Freight capacity of Sydney's intermodal terminals</title>
<link href="https://fonts.googleapis.com/css2?family=Barlow:ital,wght@0,400;0,500;0,600;0,700;0,800;1,400&display=swap" rel="stylesheet">
<style>
  :root{
    --header:#2f3c4b;
    --header-light:#45525f;
    --band:#1b8ea1;
    --band-text:#2f3c4b;
    --panel:#d3e8ec;
    --teal:#1f8a9b;
    --yellow:#f4b43c;
    --navy:#3c4757;
    --grey:#babdc0;
    --ink:#333a42;
    --rail-box:#c6c9cd;
    --road-box:#979ca3;
    --line:#4a525b;
  }
  *{margin:0;padding:0;box-sizing:border-box}
  html,body{width:1200px;height:848px;overflow:hidden;background:#fff}
  body{font-family:"Barlow",Arial,sans-serif;color:var(--ink);position:relative}

  .masthead{position:absolute;left:0;top:0;width:1200px;height:172px;background:linear-gradient(90deg,var(--header) 0%,#3a4756 60%,#4b5866 100%)}
  .masthead__frame{position:absolute;left:8px;top:8px;right:8px;bottom:0;border:1px solid rgba(255,255,255,.06);background:rgba(255,255,255,.02)}
  .masthead__title{position:absolute;left:42px;top:66px;font-size:33px;font-weight:700;color:#fff;letter-spacing:.2px}
  .masthead__art{position:absolute;left:900px;top:8px;width:290px;height:200px;background:linear-gradient(180deg,rgba(30,38,48,.55),rgba(30,38,48,.15))}

  .section-band{position:absolute;left:0;top:172px;width:1200px;height:45px;background:var(--band)}
  .section-band__label{position:absolute;left:42px;top:13px;font-size:17px;font-weight:700;letter-spacing:.6px;color:var(--band-text)}
  .section-band__label strong{color:#fff;font-weight:700}

  .chart-panel{position:absolute;left:262px;top:279px;width:595px;height:471px;background:var(--panel)}
  .axis-rule{position:absolute;left:42px;top:278px;width:815px;height:1px;background:var(--line)}
  .axis-label{position:absolute;top:254px;font-size:12px;font-weight:700;color:var(--ink)}
  .axis-ticks{position:absolute;left:373px;top:270px}
  .bottom-rule{position:absolute;left:42px;top:750px;width:815px;height:1px;background:var(--line)}

  .row{position:absolute;left:0;width:900px;height:30px}
  .row__name{position:absolute;left:42px;top:2px;font-size:18px;color:var(--ink)}
  .row__value{position:absolute;left:262px;width:80px;top:6px;text-align:right;font-size:12.5px;font-weight:700}
  .bar{position:absolute;left:373px;top:2px;height:26px;
    background-image:
      repeating-linear-gradient(90deg,transparent 0 61px,#fff 61px 63px),
      repeating-linear-gradient(90deg,rgba(255,255,255,.35) 0 1px,transparent 1px 4px);
  }
  .bar--teal{background-color:var(--teal)}
  .bar--yellow{background-color:var(--yellow)}
  .bar--navy{background-color:var(--navy)}
  .bar--grey{background-color:var(--grey)}
  .bar__more{position:absolute;left:876px;top:4px;font-size:14px;font-weight:700}

  .capacity-note{position:absolute;left:148px;top:300px;width:112px;height:52px}
  .capacity-note__text{position:absolute;left:12px;right:12px;top:4px;text-align:center;font-size:12px;font-style:italic;line-height:14px}

  .pending{position:absolute;left:262px;top:481px;width:480px;height:28px;
    background:linear-gradient(90deg,rgba(211,232,236,0) 0%,#b3d9df 30%,#b3d9df 70%,rgba(211,232,236,0) 100%)}
  .pending__text{position:absolute;left:0;right:0;top:6px;text-align:center;font-size:12.5px;font-weight:700}

  .port__title{position:absolute;left:925px;width:245px;top:229px;text-align:center;font-size:19px;font-weight:700}
  .port__sub{position:absolute;left:925px;width:245px;top:253px;text-align:center;font-size:12px;font-weight:700}
  .port__box{position:absolute;left:925px;width:215px}
  .port__box--rail{top:280px;height:206px;background:var(--rail-box)}
  .port__box--road{top:500px;height:250px;background:var(--road-box)}
  .port__icon{position:absolute;left:50%;transform:translateX(-50%)}
  .port__stat{position:absolute;left:0;right:0;text-align:center;font-size:12.5px;color:var(--ink)}
  .port__stat b{font-weight:700}
  .port__chevrons{position:absolute;left:900px;top:280px}

  .legend{position:absolute;left:42px;top:786px;width:1098px;height:57px;border:1px solid var(--line)}
  .legend__item{position:absolute;top:14px;display:flex;align-items:flex-start;gap:14px;font-size:12.5px;line-height:14px}
  .legend__swatch{width:60px;height:28px;flex:none}
</style>
</head>
<body>

<header class="masthead">
  <div class="masthead__frame"></div>
  <div class="masthead__art" role="img" aria-label="Silhouette of container gantry cranes at a port"></div>
  <h1 class="masthead__title">Freight capacity of Sydney's&nbsp; intermodal terminals</h1>
</header>

<div class="section-band">
  <div class="section-band__label"><strong>PROPOSED</strong> INTERMODALS CAPACITY</div>
</div>

<div class="chart-panel"></div>

<div class="axis-label" style="left:262px">TEUs/annum</div>
<div class="axis-label" style="left:369px">0</div>
<div class="axis-label" style="left:468px">250,000</div>
<div class="axis-label" style="left:589px">500,000</div>
<div class="axis-label" style="left:831px">1million …</div>
<div class="axis-rule"></div>
<svg class="axis-ticks" width="500" height="9" aria-hidden="true">
  <g stroke="#4a525b" stroke-width="1">
    <line x1="0.5" y1="0" x2="0.5" y2="8"/><line x1="60.5" y1="4" x2="60.5" y2="8"/>
    <line x1="121.5" y1="0" x2="121.5" y2="8"/><line x1="181.5" y1="4" x2="181.5" y2="8"/>
    <line x1="242.5" y1="0" x2="242.5" y2="8"/><line x1="302.5" y1="4" x2="302.5" y2="8"/>
    <line x1="363.5" y1="0" x2="363.5" y2="8"/><line x1="423.5" y1="4" x2="423.5" y2="8"/>
    <line x1="483.5" y1="0" x2="483.5" y2="8"/>
  </g>
</svg>

<div class="capacity-note">
  <svg width="112" height="52" aria-hidden="true" style="position:absolute;left:0;top:0">
    <g fill="none" stroke="#333a42" stroke-width="1.2">
      <path d="M8 4 Q3 4 3 10 L3 20 Q3 26 -2 26 Q3 26 3 32 L3 42 Q3 48 8 48"/>
      <path d="M104 4 Q109 4 109 10 L109 20 Q109 26 114 26 Q109 26 109 32 L109 42 Q109 48 104 48"/>
    </g>
  </svg>
  <div class="capacity-note__text">max. IMEX<br>area capacity<br>1,05 million</div>
</div>

<div class="row" style="top:294px"><span class="row__name">Moorebank</span><span class="row__value">1,700 000</span><div class="bar bar--teal" style="width:499px"></div><span class="bar__more">…</span></div>
<div class="row" style="top:331px"><span class="row__name">Tarrow</span><span class="row__value">1,000 000</span><div class="bar bar--yellow" style="width:484px"></div></div>
<div class="row" style="top:368px"><span class="row__name">Eastern Creek</span><span class="row__value">500,000</span><div class="bar bar--teal" style="width:242px"></div></div>
<div class="row" style="top:405px"><span class="row__name">Ingleburn</span><span class="row__value">70,000</span><div class="bar bar--yellow" style="width:33px"></div></div>
<div class="row" style="top:442px"><span class="row__name">Leumeah</span><span class="row__value">50,000</span><div class="bar bar--teal" style="width:24px"></div></div>
<div class="row" style="top:479px"><span class="row__name">Badgerys Creek</span></div>
<div class="pending"><div class="pending__text">still to investigate</div></div>
<div class="row" style="top:516px"><span class="row__name">Yennora</span><span class="row__value">160,000</span><div class="bar bar--teal" style="width:78px"></div></div>
<div class="row" style="top:553px"><span class="row__name">Villawood</span><span class="row__value">50,000</span><div class="bar bar--yellow" style="width:24px"></div></div>
<div class="row" style="top:590px"><span class="row__name">Minto</span><span class="row__value">200,000</span><div class="bar bar--yellow" style="width:97px"></div></div>
<div class="row" style="top:628px"><span class="row__name">Chullora</span><span class="row__value">350,000</span><div class="bar bar--navy" style="width:170px"></div></div>
<div class="row" style="top:665px"><span class="row__name">Cooks River, St Peters</span><span class="row__value">150,000</span><div class="bar bar--grey" style="width:73px"></div></div>
<div class="row" style="top:702px"><span class="row__name">Enfield</span><span class="row__value">300,000</span><div class="bar bar--yellow" style="width:145px"></div></div>
<div class="bottom-rule"></div>

<div class="port__title">Port Kelvanna</div>
<div class="port__sub">7 million TEUs/annum</div>

<svg class="port__chevrons" width="26" height="470" aria-hidden="true">
  <g fill="#c6c9cd">
    <polygon points="25,0 14,0 4,18 14,36 25,36 15,18"/>
    <polygon points="25,84 14,84 4,102 14,120 25,120 15,102"/>
    <polygon points="25,170 14,170 4,188 14,206 25,206 15,188"/>
  </g>
  <g fill="#6f757d">
    <polygon points="25,220 14,220 4,238 14,256 25,256 15,238"/>
    <polygon points="25,322 14,322 4,340 14,358 25,358 15,340"/>
    <polygon points="25,434 14,434 4,452 14,470 25,470 15,452"/>
  </g>
</svg>

<div class="port__box port__box--rail">
  <svg class="port__icon" style="top:70px" width="24" height="30" viewBox="0 0 24 30" aria-hidden="true">
    <rect x="4" y="2" width="16" height="18" rx="5" fill="#333a42"/>
    <rect x="7" y="5" width="10" height="6" fill="#c6c9cd"/>
    <circle cx="8.5" cy="16" r="1.5" fill="#c6c9cd"/><circle cx="15.5" cy="16" r="1.5" fill="#c6c9cd"/>
    <path d="M6 21 L2 28 M18 21 L22 28 M0 24 H24 M0 28 H24" stroke="#333a42" stroke-width="1.5" fill="none"/>
  </svg>
  <div class="port__stat" style="top:107px"><b>3 million by rail</b> (43%)</div>
</div>

<div class="port__box port__box--road">
  <svg class="port__icon" style="top:90px" width="48" height="24" viewBox="0 0 48 24" aria-hidden="true">
    <rect x="2" y="3" width="30" height="14" fill="#2f3c4b"/>
    <path d="M33 7 H40 L45 12 V17 H33 Z" fill="#2f3c4b"/>
    <circle cx="10" cy="18" r="3" fill="#2f3c4b" stroke="#979ca3" stroke-width="1"/>
    <circle cx="39" cy="18" r="3" fill="#2f3c4b" stroke="#979ca3" stroke-width="1"/>
    <line x1="0" y1="22.5" x2="48" y2="22.5" stroke="#2f3c4b" stroke-width="1"/>
  </svg>
  <div class="port__stat" style="top:121px"><b>4 million by road</b>&nbsp; (57%)</div>
</div>

<div class="legend">
  <div class="legend__item" style="left:12px"><div class="bar bar--yellow legend__swatch" style="position:static"></div><span>IMEX (import-export)<br>Terminal</span></div>
  <div class="legend__item" style="left:238px"><div class="bar bar--navy legend__swatch" style="position:static"></div><span style="padding-top:8px">Interstate Terminal</span></div>
  <div class="legend__item" style="left:464px"><div class="bar bar--teal legend__swatch" style="position:static"></div><span style="padding-top:8px">IMEX &amp; Interstate</span></div>
  <div class="legend__item" style="left:688px"><div class="bar bar--grey legend__swatch" style="position:static"></div><span style="padding-top:8px">Storage Empty Containers</span></div>
</div>

</body>
</html>
```